Bref créative
Velmora Stationery
Letterhead and business card
I need double sided standard sized Business Card [3.5" x 2"]
Anything
Professional
Renee Harlow
Professional Engineer
4817 North 62nd Avenue
Harwick, NE 58261
604.2875.PRO
renee@velmora-example.com
http://velmora-example.com
Tagline "Your plans stay on course"
Velmora logo chosen from logo design contest

```html
<!DOCTYPE html>
<html lang="en">
<head>
<meta charset="utf-8">
<title>Velmora Stationery – Business Cards</title>
<link rel="stylesheet" href="https://fonts.googleapis.com/css2?family=Marcellus+SC&family=Open+Sans:wght@400;600;700&display=swap">
<style>
  :root {
    --backdrop: #e9e4dc;
    --card-white: #ffffff;
    --silver-light: #f4f4f4;
    --silver-dark: #8f8f8f;
    --brand-red: #8e1b20;
    --ink: #3a3a3a;
    --ink-soft: #555555;
    --divider: #b8b8b8;
    --label: #3b3b3b;
  }
  * { margin: 0; padding: 0; box-sizing: border-box; }
  html, body { width: 1200px; height: 794px; overflow: hidden; }
  body { background: var(--backdrop); font-family: "Open Sans", Arial, sans-serif; position: relative; }

  .card {
    position: absolute;
    width: 495px; height: 272px;
    border-radius: 24px;
    box-shadow: 0 2px 6px rgba(0,0,0,.25);
    overflow: hidden;
  }
  .card--white { background: var(--card-white); }
  .card--silver { background: radial-gradient(ellipse at 50% 40%, var(--silver-light) 0%, #cfcfcf 55%, var(--silver-dark) 100%); }

  .front-a { left: 78px;  top: 46px; }
  .front-b { left: 630px; top: 44px; }
  .back-a  { left: 78px;  top: 412px; }
  .back-b  { left: 630px; top: 412px; }

  .card-label {
    position: absolute;
    width: 495px;
    text-align: center;
    font-family: "Marcellus SC", serif;
    font-size: 23px;
    letter-spacing: 3px;
    color: var(--label);
  }
  .label-top { top: 344px; }
  .label-bottom { top: 728px; }
  .label-left { left: 78px; }
  .label-right { left: 630px; }

  .brand {
    position: absolute; left: 28px; top: 100px;
    width: 218px;
  }
  .brand-row { display: flex; align-items: center; gap: 10px; }
  .brand-dot { width: 22px; height: 22px; border-radius: 50%; background: var(--brand-red); flex: none; }
  .brand-name {
    font-size: 38px; font-weight: 600; letter-spacing: 1px;
    color: var(--brand-red); line-height: 1;
  }
  .brand-tagline {
    margin-top: 6px;
    font-size: 14px; color: var(--ink-soft);
    white-space: nowrap;
  }

  .divider {
    position: absolute; left: 258px; top: 36px;
    width: 1px; height: 150px; background: var(--divider);
  }

  .contact { position: absolute; left: 272px; top: 34px; width: 210px; }
  .contact-name { font-size: 15px; font-weight: 700; color: var(--brand-red); line-height: 1.2; }
  .contact-title { font-size: 11.5px; color: var(--ink); margin-bottom: 12px; }
  .contact-line { display: flex; align-items: flex-start; gap: 8px; font-size: 10.5px; color: var(--ink); line-height: 1.35; margin-bottom: 4px; white-space: nowrap; }
  .contact-line svg { flex: none; width: 10px; height: 10px; margin-top: 3px; fill: var(--brand-red); }

  .back-tagline {
    position: absolute; inset: 0;
    display: flex; align-items: center; justify-content: center;
    font-size: 21px; color: var(--ink);
  }
</style>
</head>
<body>

  <section class="card card--white front-a">
    <div class="brand">
      <div class="brand-row"><span class="brand-dot"></span><span class="brand-name">Velmora</span></div>
      <p class="brand-tagline">Your plans stay on course</p>
    </div>
    <div class="divider"></div>
    <div class="contact">
      <p class="contact-name">Renee Harlow</p>
      <p class="contact-title">Professional Engineer</p>
      <p class="contact-line"><svg viewBox="0 0 10 10"><path d="M5 0a3.5 3.5 0 0 0-3.5 3.5C1.5 6 5 10 5 10s3.5-4 3.5-6.5A3.5 3.5 0 0 0 5 0zm0 5a1.5 1.5 0 1 1 0-3 1.5 1.5 0 0 1 0 3z"/></svg><span>4817 North 62nd Avenue<br>Harwick, NE 58261</span></p>
      <p class="contact-line"><svg viewBox="0 0 10 10"><path d="M2 0l2 2.5-1.2 1.3a6 6 0 0 0 3.4 3.4L7.5 6 10 8 8.5 10C4 10 0 6 0 1.5z"/></svg><span>604.2875.PRO</span></p>
      <p class="contact-line"><svg viewBox="0 0 10 10"><path d="M0 2h10v6H0zM0 2l5 3.5L10 2" stroke="#fff" stroke-width=".8"/></svg><span>renee@velmora-example.com</span></p>
      <p class="contact-line"><svg viewBox="0 0 10 10"><circle cx="5" cy="5" r="5"/></svg><span>http://velmora-example.com</span></p>
    </div>
  </section>
  <p class="card-label label-top label-left">Business Card Front A</p>

  <section class="card card--silver front-b">
    <div class="brand">
      <div class="brand-row"><span class="brand-dot"></span><span class="brand-name">Velmora</span></div>
      <p class="brand-tagline">Your plans stay on course</p>
    </div>
    <div class="divider"></div>
    <div class="contact">
      <p class="contact-name">Renee Harlow</p>
      <p class="contact-title">Professional Engineer</p>
      <p class="contact-line"><svg viewBox="0 0 10 10"><path d="M5 0a3.5 3.5 0 0 0-3.5 3.5C1.5 6 5 10 5 10s3.5-4 3.5-6.5A3.5 3.5 0 0 0 5 0zm0 5a1.5 1.5 0 1 1 0-3 1.5 1.5 0 0 1 0 3z"/></svg><span>4817 North 62nd Avenue<br>Harwick, NE 58261</span></p>
      <p class="contact-line"><svg viewBox="0 0 10 10"><path d="M2 0l2 2.5-1.2 1.3a6 6 0 0 0 3.4 3.4L7.5 6 10 8 8.5 10C4 10 0 6 0 1.5z"/></svg><span>604.2875.PRO</span></p>
      <p class="contact-line"><svg viewBox="0 0 10 10"><path d="M0 2h10v6H0zM0 2l5 3.5L10 2" stroke="#ddd" stroke-width=".8"/></svg><span>renee@velmora-example.com</span></p>
      <p class="contact-line"><svg viewBox="0 0 10 10"><circle cx="5" cy="5" r="5"/></svg><span>http://velmora-example.com</span></p>
    </div>
  </section>
  <p class="card-label label-top label-right">Business Card Front B</p>

  <section class="card card--white back-a">
    <p class="back-tagline">Your plans stay on course</p>
  </section>
  <p class="card-label label-bottom label-left">Business Card Back A</p>

  <section class="card card--silver back-b">
    <p class="back-tagline">Your plans stay on course</p>
  </section>
  <p class="card-label label-bottom label-right">Business Card Back B</p>

</body>
</html>
```